Global (re)insurance broker needs a business card design

We need a classic business card for our company that is headquartered in SG, with offices in Malaysia and Dubai. We specialise in insurance and reinsurance broking and consultancy for our global clients.

```html
<!DOCTYPE html>
<html lang="en">
<head>
<meta charset="utf-8">
<title>Norvane business card</title>
<link rel="stylesheet" href="https://fonts.googleapis.com/css2?family=Open+Sans:wght@400;600;700&display=swap">
<style>
  :root {
    --backdrop: #2b2b2d;
    --card: #ffffff;
    --brand-blue: #2448a0;
    --brand-green: #c3deb8;
    --ink: #1c1c1c;
    --rule: #2a2a2a;
  }
  * { box-sizing: border-box; margin: 0; padding: 0; }
  html, body { width: 1200px; height: 780px; overflow: hidden; }
  body {
    background: var(--backdrop);
    font-family: "Open Sans", Arial, sans-serif;
    color: var(--ink);
    display: flex;
    align-items: center;
    justify-content: center;
    gap: 30px;
  }
  .card {
    position: relative;
    width: 560px;
    height: 320px;
    background: var(--card);
    border-radius: 22px;
    overflow: hidden;
  }
  .band {
    position: absolute;
    left: 0; right: 0; bottom: 0;
    height: 20px;
  }
  .band-blue {
    position: absolute; left: 0; top: 0; bottom: 0;
    width: 47%;
    background: var(--brand-blue);
    clip-path: polygon(0 0, 97% 0, 100% 100%, 0 100%);
  }
  .band-green {
    position: absolute; right: 0; top: 0; bottom: 0;
    width: 51%;
    background: var(--brand-green);
    clip-path: polygon(0 0, 100% 0, 100% 100%, 3% 100%);
  }
  .wordmark {
    font-weight: 700;
    color: var(--brand-blue);
    letter-spacing: 1px;
    line-height: 1;
  }
  /* front side */
  .card-front .wordmark {
    position: absolute;
    left: 38px; top: 78px;
    font-size: 40px;
  }
  .divider {
    position: absolute;
    left: 270px; top: 70px;
  }
  .person {
    position: absolute;
    left: 312px; top: 96px;
  }
  .person-name {
    font-size: 30px;
    font-weight: 700;
    line-height: 1.05;
  }
  .person-name .first { color: var(--brand-blue); }
  .person-name .last { color: var(--brand-green); }
  .person-title {
    font-size: 15px;
    font-weight: 600;
    margin-top: 2px;
  }
  .contacts {
    list-style: none;
    margin-top: 14px;
    font-size: 14px;
  }
  .contacts li {
    display: flex;
    align-items: center;
    gap: 8px;
    line-height: 1.55;
  }
  .contacts svg { width: 12px; height: 12px; flex: none; }
  .address {
    position: absolute;
    left: 38px; bottom: 34px;
    font-size: 13px;
  }
  /* back side */
  .card-back .wordmark {
    position: absolute;
    left: 0; right: 0; top: 118px;
    text-align: center;
    font-size: 64px;
  }
</style>
</head>
<body>
  <section class="card card-front" aria-label="Business card front">
    <div class="wordmark">NORVANE</div>
    <svg class="divider" width="40" height="140" viewBox="0 0 40 140" aria-hidden="true">
      <line x1="38" y1="0" x2="2" y2="140" stroke="var(--rule)" stroke-width="1"/>
    </svg>
    <div class="person">
      <h1 class="person-name"><span class="first">Mira</span> <span class="last">Lowe</span></h1>
      <p class="person-title">Chief Operating Officer</p>
      <ul class="contacts">
        <li>
          <svg viewBox="0 0 12 12" aria-hidden="true"><rect x="3" y="1" width="6" height="10" rx="1" fill="none" stroke="var(--brand-blue)"/></svg>
          +65 9000 1234
        </li>
        <li>
          <svg viewBox="0 0 12 12" aria-hidden="true"><circle cx="6" cy="6" r="5.5" fill="var(--brand-blue)"/><path d="M0.5 6h11M6 0.5v11" stroke="#fff" stroke-width="0.8"/></svg>
          www.norvane.com
        </li>
        <li>
          <svg viewBox="0 0 12 12" aria-hidden="true"><rect x="0.5" y="2" width="11" height="8" fill="none" stroke="var(--brand-green)"/><path d="M0.5 2l5.5 4.5 5.5-4.5" fill="none" stroke="var(--brand-green)"/></svg>
          mira@norvane.com
        </li>
      </ul>
    </div>
    <p class="address">22 Harbour Lane, Meridian Tower #08-04, Singapore 068800</p>
    <div class="band"><span class="band-blue"></span><span class="band-green"></span></div>
  </section>

  <section class="card card-back" aria-label="Business card back">
    <div class="wordmark">NORVANE</div>
    <div class="band"><span class="band-blue"></span><span class="band-green"></span></div>
  </section>
</body>
</html>
```